Elegant and modern Wedding Photography brochure

My existing brochure (attached) needs a major facelift. This is one of the main selling tools - it gets emailed to my clients when they make an equiry on what packages i offer and it is printed out and walked through at our first meeting. This brochure is as critical as my website - it needs to sing!

I'm looking for an eye-catching design that says:
Elegant
Modern
Clean
Crisp
Not cutesy or lovey-dovey thanks - we are more sophisticated and professional than that.

Update images to some of the latest weddings I've shot also. Let me know files and resolution you need. I've enabled right-click to download images on my site for a limited time. Please note that I retain copyright and will pursue any breeches.

Http://www.sarahkelbrin.com/Melbourne-wedding-photography
Updates

Thanks for all of your designs! Will take a few days to decide.

Target Market(s)

Australian Women aged 24-44

Industry/Entity Type

Wedding

Font styles to use
Other font styles liked:
• Century Gothic

Requirements
Must have
• Easy to print - does not have to be 6 A4 pages like the existing brochure
Nice to have
• Some full page images - The photos are supposed to be the hero here :-)
Should not have
• Not cutesy or lovey-dovey thanks - we are more sophisticated and professional than that.

No black backgrounds, I prefer a white thanks

No images in organic shaped boxes (like the rectangles in the logo - no thanks).
Keep the lines straight and sharp

```html
<!DOCTYPE html>
<html lang="en">
<head>
<meta charset="utf-8">
<title>A la Carte Fees to Consider</title>
<link rel="stylesheet" href="https://fonts.googleapis.com/css2?family=Cormorant+Garamond:ital,wght@0,300;0,500;1,500&family=Didact+Gothic&display=swap">
<style>
  :root {
    --page: #ffffff;
    --band: #ece7f0;
    --band-fade: rgba(236, 231, 240, 0);
    --rule: #b9aec4;
    --title: #5f5650;
    --initial: #8a7d74;
    --heading: #3f9b58;
    --body: #4d4540;
    --frame: #ffffff;
    --frame-line: #e4e0dc;
  }
  * { box-sizing: border-box; margin: 0; padding: 0; }
  html, body { width: 1200px; height: 913px; overflow: hidden; }
  body {
    position: relative;
    background: var(--page);
    font-family: "Didact Gothic", "Century Gothic", sans-serif;
    color: var(--body);
  }
  .title-band {
    position: absolute;
    left: 420px; top: 133px;
    width: 780px; height: 31px;
    background: linear-gradient(90deg, var(--band-fade) 0%, var(--band) 10%, var(--band) 82%, var(--band-fade) 100%);
    border-bottom: 1px solid var(--rule);
  }
  .title-initial {
    position: absolute;
    left: 440px; top: 28px;
    font-family: "Cormorant Garamond", Georgia, serif;
    font-weight: 300;
    font-size: 170px;
    line-height: 1;
    color: var(--initial);
  }
  .title-text {
    position: absolute;
    left: 552px; top: 131px;
    font-family: "Didact Gothic", "Century Gothic", sans-serif;
    font-weight: 400;
    font-size: 29px;
    line-height: 34px;
    letter-spacing: 1px;
    color: var(--title);
  }
  .photo {
    position: absolute;
    border: 10px solid var(--frame);
    outline: 1px solid var(--frame-line);
    box-shadow: 0 4px 12px rgba(40, 30, 20, 0.22);
  }
  .photo-portrait {
    left: 45px; top: 230px; width: 330px; height: 218px;
    background: linear-gradient(120deg, #7d7a52 0%, #cfc1a8 45%, #e9e2d8 70%, #8e8a63 100%);
    z-index: 2;
  }
  .photo-couple {
    left: 10px; top: 400px; width: 678px; height: 452px;
    background: linear-gradient(100deg, #6f6a3e 0%, #c9b99a 40%, #e8e2d6 55%, #3b3a35 68%, #6f6a3e 100%);
    z-index: 1;
  }
  .fees {
    position: absolute;
    left: 728px; top: 204px;
    width: 430px;
    list-style: none;
  }
  .fee-name {
    font-family: "Cormorant Garamond", Georgia, serif;
    font-style: italic;
    font-weight: 500;
    font-size: 19px;
    line-height: 24px;
    color: var(--heading);
  }
  .fee-items {
    list-style: none;
    margin-left: 35px;
    margin-bottom: 3px;
  }
  .fee-items li {
    position: relative;
    font-size: 13px;
    line-height: 19px;
    padding-left: 16px;
  }
  .fee-items li::before {
    content: "";
    position: absolute;
    left: 0; top: 8px;
    width: 4px; height: 4px;
    background: var(--body);
  }
</style>
</head>
<body>
  <div class="title-band"></div>
  <div class="title-initial">A</div>
  <h1 class="title-text">la Carte Fees to Consider</h1>

  <div class="photo photo-couple" role="img" aria-label="Bride and groom embracing beneath willow trees"></div>
  <div class="photo photo-portrait" role="img" aria-label="Portrait of the bride in her veil"></div>

  <ul class="fees">
    <li><h2 class="fee-name">Engagement Session/Pre-wedding Shoot</h2>
      <ul class="fee-items"><li>$290 for up to 2 hours of photography on location</li></ul></li>
    <li><h2 class="fee-name">Digital Negatives</h2>
      <ul class="fee-items"><li>$490</li></ul></li>
    <li><h2 class="fee-name">Extended Coverage</h2>
      <ul class="fee-items"><li>$160 per hour</li></ul></li>
    <li><h2 class="fee-name">Web Gallery &amp; Social Feed posting</h2>
      <ul class="fee-items"><li>$160</li></ul></li>
    <li><h2 class="fee-name">Slideshow</h2>
      <ul class="fee-items"><li>$250</li></ul></li>
    <li><h2 class="fee-name">Second Photographer</h2>
      <ul class="fee-items"><li>$590</li></ul></li>
    <li><h2 class="fee-name">Clients for life</h2>
      <ul class="fee-items"><li>No sitting fees for portrait sessions – Anniversaries, family portraits, etc $390</li></ul></li>
    <li><h2 class="fee-name">Photo Enlargements</h2>
      <ul class="fee-items">
        <li>Quality custom archival prints in a variety of sizes 5x7 up to 8x10 $25, 12.5x18.5 $50</li>
        <li>Stretched Canvas Prints for your wall Various sizes available from 16"x20" starting at $395 through to 60"x96" $1500</li>
        <li>Plus many other options!</li>
      </ul></li>
    <li><h2 class="fee-name">Professionally Edited Album (Regular)</h2>
      <ul class="fee-items"><li>$790</li></ul></li>
    <li><h2 class="fee-name">Album Upgrade from Regular to Signature Grand</h2>
      <ul class="fee-items">
        <li>From Gold Package to Signature Grand: $1150</li>
        <li>From Platinum Package to Signature Grand: $650</li>
      </ul></li>
    <li><h2 class="fee-name">Custom Thank-you Cards</h2>
      <ul class="fee-items"><li>$150 for 50 cards (174mm x 123mm) including envelopes</li></ul></li>
  </ul>
</body>
</html>
```